Coastline Premier Retreats Business Card Design

Design a business card for Coastline Premier Retreats. Look at the website for colors and reference. Card should have logo, name, title, office number, mobile number, email, URL and a tagline like, "Luxury Hotel & Resort Email Marketing" (This might change).

https://www.coastlinepremierretreats.example

The rest I will leave up to your imagination.

Contact Information for Business Card

Logo, name, title, office number, mobile number, email, URL and a tagline like, "Luxury Hotel & Resort Email Marketing" (This might change).

```html
<!DOCTYPE html>
<html lang="en">
<head>
<meta charset="utf-8">
<title>Coastline Premier Retreats – Business Card</title>
<link rel="stylesheet" href="https://fonts.googleapis.com/css2?family=Montserrat:wght@400;500;700;800&family=Open+Sans:ital,wght@1,400&display=swap">
<style>
  :root {
    --backdrop: #2b2b2b;
    --card: #1b1b1b;
    --orange: #f07416;
    --white: #ffffff;
    --mark-grey: #4a4a4a;
  }
  * { box-sizing: border-box; margin: 0; padding: 0; }
  html, body {
    width: 1200px; height: 900px; overflow: hidden;
    background: var(--backdrop);
  }
  .canvas {
    width: 1200px; height: 900px;
    display: flex; flex-direction: column; align-items: center; justify-content: center;
    gap: 40px;
  }
  .card {
    position: relative;
    width: 700px; height: 400px;
    background: var(--card);
    box-shadow: 0 10px 30px rgba(0,0,0,.45);
    overflow: hidden;
    font-family: "Montserrat", sans-serif;
  }

  /* Front */
  .brand {
    position: absolute; left: 48px; top: 136px; width: 256px;
    display: flex; align-items: center; gap: 12px;
  }
  .brand-square { width: 16px; height: 16px; background: var(--orange); flex: none; }
  .brand-name {
    color: var(--white); font-weight: 800; font-size: 18px; line-height: 1.2;
    letter-spacing: .5px; text-transform: uppercase; white-space: nowrap;
  }
  .divider {
    position: absolute; left: 326px; top: 70px;
    width: 1px; height: 230px; background: var(--orange);
  }
  .details { position: absolute; left: 350px; top: 74px; right: 16px; color: var(--white); }
  .person-name {
    color: var(--orange); font-weight: 800; font-size: 30px; letter-spacing: .5px;
    text-transform: uppercase; line-height: 1; white-space: nowrap;
  }
  .person-title { font-size: 15px; font-weight: 500; margin-top: 6px; }
  .address { font-size: 14px; line-height: 1.45; margin-top: 16px; }
  .contact-list { list-style: none; margin-top: 14px; font-size: 13.5px; line-height: 1.55; }
  .contact-list li { display: flex; align-items: center; gap: 9px; white-space: nowrap; }
  .contact-list svg { width: 12px; height: 12px; flex: none; fill: var(--orange); }
  .url-accent { color: var(--orange); }
  .accent-band {
    position: absolute; left: 0; right: 0; bottom: 0; height: 18px;
    background: var(--orange);
  }

  /* Back */
  .back-mark {
    position: absolute; left: 0; right: 0; top: 92px;
    display: flex; justify-content: center; align-items: center; gap: 22px;
  }
  .back-mark-square { width: 34px; height: 34px; background: var(--mark-grey); flex: none; }
  .back-mark-name {
    color: var(--mark-grey); font-weight: 800; font-size: 44px; line-height: 1.05;
    letter-spacing: 2px; text-transform: uppercase;
  }
  .tagline {
    position: absolute; left: 0; right: 0; bottom: 92px; text-align: center;
    font-family: "Open Sans", sans-serif; font-style: italic;
    color: var(--orange); font-size: 24px;
  }
</style>
</head>
<body>
<main class="canvas">

  <section class="card card-front" aria-label="Business card front">
    <div class="brand">
      <span class="brand-square"></span>
      <p class="brand-name">Coastline<br>Premier Retreats</p>
    </div>
    <span class="divider"></span>
    <div class="details">
      <h1 class="person-name">Daniel Morrow</h1>
      <p class="person-title">CEO/Founder</p>
      <p class="address">PO Box 48, 17 Harbor Lane<br>Bayfield, NA 40512</p>
      <ul class="contact-list">
        <li>
          <svg viewBox="0 0 12 12" aria-hidden="true"><path d="M3 0h6a1 1 0 0 1 1 1v10a1 1 0 0 1-1 1H3a1 1 0 0 1-1-1V1a1 1 0 0 1 1-1zm0 1.5v8h6v-8zM5.5 10.2h1v.8h-1z"/></svg>
          555.014.2870
        </li>
        <li>
          <svg viewBox="0 0 12 12" aria-hidden="true"><path d="M2.4 1 4.2.6 5.5 3.3 4.3 4.4a7 7 0 0 0 3.3 3.3l1.1-1.2 2.7 1.3-.4 1.8A1.6 1.6 0 0 1 9.4 11 8.6 8.6 0 0 1 1 2.6 1.6 1.6 0 0 1 2.4 1z"/></svg>
          +34 600 000 417
        </li>
        <li>
          <svg viewBox="0 0 12 12" aria-hidden="true"><path d="M0 2h12v8H0zm1 1v.4l5 3.2 5-3.2V3zm0 1.6V9h10V4.6L6 7.8z"/></svg>
          info@coastlinepremierretreats.example
        </li>
        <li>
          <svg viewBox="0 0 12 12" aria-hidden="true"><path d="M6 0a6 6 0 1 0 0 12A6 6 0 0 0 6 0zm0 1a5 5 0 0 1 4.5 2.9H8.3A7.6 7.6 0 0 0 7 1.1 5 5 0 0 1 6 1zm-1 .1a7.6 7.6 0 0 0-1.3 2.8H1.5A5 5 0 0 1 5 1.1zM1.1 5h2.5a9 9 0 0 0 0 2H1.1a5 5 0 0 1 0-2zm3.5 0h2.8a9 9 0 0 1 0 2H4.6a9 9 0 0 1 0-2zm3.8 0h2.5a5 5 0 0 1 0 2H8.4a9 9 0 0 0 0-2zM1.5 8.1h2.2A7.6 7.6 0 0 0 5 10.9a5 5 0 0 1-3.5-2.8zm6.8 0h2.2A5 5 0 0 1 7 10.9a7.6 7.6 0 0 0 1.3-2.8z"/></svg>
          <span>www.<span class="url-accent">coastlinepremierretreats</span>.example</span>
        </li>
      </ul>
    </div>
    <span class="accent-band"></span>
  </section>

  <section class="card card-back" aria-label="Business card back">
    <div class="back-mark">
      <span class="back-mark-square"></span>
      <p class="back-mark-name">Coastline<br>Premier Retreats</p>
    </div>
    <p class="tagline">Luxury Hotel &amp; Resort Email Marketing</p>
  </section>

</main>
</body>
</html>
```